Cat-products company needs smart, yet endearing, business card

We need a business card design for a new, but up-and-running, business based in Honolulu, Hawaii. The business is Purrnest Nook Co. Our first product is the most environmentally-friendly cat grass kit ever seen on the planet. Future products, currently in the R&D phase, will include a variety of exciting cat scratchers. We also do consulting work to help apartment-dwellers make their home more cat-friendly and, in the future, plan on doing full, custom installs of structure to create high walkways for cats.

Target Market(s)

Middle-aged, apartment-dwelling, middle-class workers who own 1 or more cats and who dote on them.

Industry/Entity Type

Pet Care

Contact Information for Business Card

A striking, professional, yet warm and friendly design is what we're after.

Font styles to use
Serif
Sans Serif
Other font styles liked:
• Comfortaa

Colors

Designer to choose colors to be used in the design.

Requirements
Must have
• The company logo: (see attachment)
• The company name: Purrnest Nook Co
• The web address: www.purrnestnookco.com
• Email: support@purrnestnookco.com
• Phone: +1 (808) 571 6023
• Update (Fri Jun 30 3017 7:45pm Hawaii Time) I would like, is possible, uploaded picture of the cat grass kit on the back of the card with some text along the lines of: Purrnest Nook Co - Maker Of The Leafiest Feline Sprout Set Yet
Nice to have
• A cat picture, cartoon, real or silhouette that illustrates cats in action and/or relaxing; ie using the apartment space to live, play and relax in and being well-contented.
• Most of the website is done in the font: Comfortaa. It might be nice to continue using this for brand consistency.
Should not have
• Hard-to-read fonts.

```html
<!DOCTYPE html>
<html lang="en">
<head>
<meta charset="utf-8">
<title>Purrnest Nook Co – Business Card</title>
<link href="https://fonts.googleapis.com/css2?family=Source+Sans+3:wght@400;600;700&display=swap" rel="stylesheet">
<style>
  :root {
    --stage: #222222;
    --card-light: #f2f2f2;
    --cocoa: #5a3630;
    --honey: #f9b21a;
    --ink: #1e1e1e;
    --rule: #555555;
    --white: #ffffff;
  }
  * { box-sizing: border-box; margin: 0; padding: 0; }
  html, body {
    width: 1200px; height: 900px; overflow: hidden;
    background: var(--stage);
    font-family: "Source Sans 3", "Myriad Pro", sans-serif;
  }
  .stage { position: relative; width: 1200px; height: 900px; }
  .card {
    position: absolute; top: 170px;
    width: 347px; height: 561px;
  }
  .card-front { left: 259px; background: var(--card-light); }
  .card-back { left: 631px; background: var(--cocoa); }

  .brand-mark {
    position: absolute; left: 0; right: 0; top: 60px;
    display: flex; flex-direction: column; align-items: center; gap: 28px;
  }
  .brand-dot {
    width: 96px; height: 96px; border-radius: 50%;
    background: var(--honey);
  }
  .brand-name {
    font-size: 38px; font-weight: 700; color: var(--cocoa);
    line-height: 1.05; text-align: center;
  }

  .holder {
    position: absolute; left: 0; right: 0; top: 358px; text-align: center;
  }
  .holder-name {
    font-size: 21px; font-weight: 700; color: var(--honey);
    letter-spacing: 0.3px; line-height: 1;
  }
  .holder-role {
    margin-top: 7px; font-size: 15px; color: var(--ink); line-height: 1;
  }
  .divider {
    width: 122px; height: 1px; background: var(--rule);
    margin: 15px auto 0;
  }
  .contact-icons {
    display: flex; justify-content: center; gap: 5px; margin-top: 16px;
  }
  .contact-icons svg { width: 14px; height: 14px; fill: var(--honey); }
  .contact-list {
    list-style: none; margin-top: 9px;
    font-size: 15.5px; color: var(--ink); line-height: 20.5px;
  }

  .back-mark {
    position: absolute; left: 0; right: 0; top: 170px;
    display: flex; flex-direction: column; align-items: center; gap: 30px;
  }
  .back-dot {
    width: 130px; height: 130px; border-radius: 50%;
    background: var(--honey);
  }
  .back-name {
    font-size: 40px; font-weight: 700; color: var(--white);
    line-height: 1.05; text-align: center;
  }
</style>
</head>
<body>
<main class="stage">
  <section class="card card-front">
    <div class="brand-mark">
      <div class="brand-dot"></div>
      <div class="brand-name">Purrnest<br>Nook Co</div>
    </div>

    <div class="holder">
      <div class="holder-name">KALANI REYES</div>
      <div class="holder-role">Managing Director</div>
      <div class="divider"></div>
      <div class="contact-icons" aria-hidden="true">
        <svg viewBox="0 0 24 24"><path d="M6.6 10.8a15.1 15.1 0 0 0 6.6 6.6l2.2-2.2a1 1 0 0 1 1-.25 11.4 11.4 0 0 0 3.6.57 1 1 0 0 1 1 1V20a1 1 0 0 1-1 1A17 17 0 0 1 3 4a1 1 0 0 1 1-1h3.5a1 1 0 0 1 1 1c0 1.25.2 2.45.57 3.57a1 1 0 0 1-.25 1z"/></svg>
        <svg viewBox="0 0 24 24"><path d="M2 5h20v14H2z M3.5 6.5 12 13l8.5-6.5" fill="var(--honey)"/><path d="M3 6l9 7 9-7" fill="none" stroke="var(--card-light)" stroke-width="1.6"/></svg>
        <svg viewBox="0 0 24 24"><circle cx="12" cy="12" r="10"/><path d="M7 6c2 1 3 3 2 5s-3 1-3 4M14 3c-1 2 1 3 2 4s3 0 4 2M15 20c0-3 2-3 3-5" fill="none" stroke="var(--card-light)" stroke-width="1.6"/></svg>
      </div>
      <ul class="contact-list">
        <li>+1 (808) 571 6023</li>
        <li>support@purrnestnookco.com</li>
        <li>www.purrnestnookco.com</li>
      </ul>
    </div>
  </section>

  <section class="card card-back">
    <div class="back-mark">
      <div class="back-dot"></div>
      <div class="back-name">Purrnest<br>Nook Co</div>
    </div>
  </section>
</main>
</body>
</html>
```